We need a complete design for our construction company KELTO CONSTRUCTION based in Auckland New Zealand, we need a logo, website, business card, vehicle design etc..
We are a mid to high-end construction company who work mostly on residential projects and some commercial.

What we want to see in the design;
Professional,
Architectural,
Simple,
Alternative,

We want the design to communicate professionalism, high quality wormanship and and quality service.

Target Market(s)

People looking for a quality building/ construction company

Industry/Entity Type

Construction Company

Contact Information for Business Card

KELTO CONSTRUCTION.co.nz
Lino Verasek
lino@keltoconstruction.example.nz
021 5807 462

Logo Text

KELTO CONSTRUCTION

Number of Pages Required

5+ page

Font styles to use
Sans Serif

Colors

Designer to choose colors to be used in the design.

Requirements
Must have
• Must appear high end, professional, quality, be simple, easy to use, give security to potential clients
Nice to have
• high-quality photos of our recent projects
• about us page
• blog page
• contact us page
• high quality content
Should not have
• should not be hard to use and have too much going on.

```html
<!DOCTYPE html>
<html lang="en">
<head>
<meta charset="utf-8">
<title>Kelto Construction</title>
<link href="https://fonts.googleapis.com/css2?family=Orbitron:wght@400;500&family=Questrial&display=swap" rel="stylesheet">
<style>
:root{
  --coral:#e8584a;
  --navy:#24384d;
  --ink:#222;
  --muted:#9a9a9a;
  --soft:#f1f1f1;
  --line:#cfcfcf;
  --night:#0b0b0b;
}
*{box-sizing:border-box;margin:0;padding:0}
html,body{width:1200px;height:3390px;overflow:hidden;background:#fff}
body{position:relative;font-family:"Questrial",sans-serif;color:var(--ink)}
.abs{position:absolute}
.heading{font-family:"Orbitron",sans-serif;color:var(--coral);font-weight:400;letter-spacing:8px;text-transform:uppercase}
.body-copy{font-size:15px;line-height:25px;color:var(--muted)}
.btn{position:absolute;border:2px solid var(--coral);color:var(--coral);font-size:18px;letter-spacing:1.5px;display:flex;align-items:center;justify-content:center;text-transform:uppercase;background:transparent}
.photo{position:absolute}
.frame{position:absolute;border:5px solid #ddd}

/* header */
.site-header{position:absolute;left:0;top:0;width:1200px;height:124px;background:#fff}
.brand{left:77px;top:40px;font-size:30px;letter-spacing:5px;color:var(--navy)}
.nav{position:absolute;top:52px;left:568px;display:flex;gap:0}
.nav a{position:absolute;font-size:13px;letter-spacing:1px;color:#8a8a8a;text-decoration:none;white-space:nowrap}
.nav .current{color:var(--coral);border:2px solid var(--coral);padding:4px 8px;top:-6px}

/* hero */
.hero{left:0;top:124px;width:1200px;height:576px;background:linear-gradient(180deg,#1e2e44 0%,#52657a 45%,#9aa3ab 75%,#6c6c6c 100%)}
.hero-panel{left:75px;top:228px;width:718px;height:371px;border:7px solid rgba(255,255,255,.35);background:rgba(30,40,55,.45)}
.hero-brand{left:120px;top:282px;font-size:64px;letter-spacing:14px}
.hero-title{left:122px;top:362px;font-size:25px;color:#fff;font-family:"Orbitron",sans-serif;letter-spacing:1px}
.hero-copy{left:122px;top:412px;width:640px;font-size:14px;line-height:22px;color:#c9d0d8}
.hero-btn{left:118px;top:477px;width:256px;height:63px;color:#fff}
.slider-arrow{position:absolute;width:56px;height:56px;border:2px solid rgba(255,255,255,.7);border-radius:50%;display:flex;align-items:center;justify-content:center}

/* about */
.about-title{left:81px;top:760px;font-size:50px}
.about-copy{left:81px;top:836px;width:490px}
.about-btn{left:81px;top:1015px;width:172px;height:56px}

/* projects */
.projects{left:0;top:1168px;width:1200px;height:769px;background:var(--soft)}
.projects-title{left:707px;top:1290px;font-size:50px}
.projects-copy{left:707px;top:1358px;width:420px}
.projects-btn{left:703px;top:1505px;width:269px;height:57px}
.thumb{position:absolute;top:1722px;width:245px;height:154px}

/* testimonial */
.testimonial{left:0;top:1937px;width:1200px;height:416px;background:var(--coral)}
.quote-box{left:255px;top:2016px;width:688px;height:154px;border:2px solid rgba(255,255,255,.65)}
.quote{left:300px;top:2050px;width:600px;text-align:center;font-style:italic;font-size:17px;line-height:21px;color:#fff}
.cite{left:480px;top:2182px;font-family:"Orbitron",sans-serif;font-size:15px;letter-spacing:2px;color:#fff}
.cite-role{left:622px;top:2208px;font-size:13px;color:#fde3df}
.avatar{left:714px;top:2134px;width:84px;height:84px;border:3px solid #fff;background:linear-gradient(135deg,#e7c79f,#b5835a)}
.dot{position:absolute;top:2260px;width:9px;height:9px;border:1px solid #fff}

/* blogs */
.blogs-title{left:81px;top:2466px;font-size:50px}
.post-img{position:absolute;left:77px;width:199px;height:177px}
.post-date{position:absolute;left:286px;font-size:13px;color:#777;display:flex;align-items:center;gap:10px}
.post-title{position:absolute;left:286px;font-size:17px;color:var(--ink)}
.post-copy{position:absolute;left:286px;width:250px;font-size:13px;line-height:19px;color:var(--muted)}
.post-more{position:absolute;left:286px;font-size:14px;color:var(--coral);text-decoration:underline;letter-spacing:1px}
.feature-card{left:581px;top:2448px;width:459px;height:350px;background:#fff}
.date-badge{left:768px;top:2448px;width:80px;height:83px;background:#2c2c2c;color:#fff;text-align:center}
.feature-title{left:581px;top:2566px;width:459px;text-align:center;font-size:24px;color:var(--ink)}
.feature-copy{left:600px;top:2612px;width:421px;text-align:center;font-size:13px;line-height:19px;color:var(--muted)}
.feature-btn{left:730px;top:2703px;width:176px;height:57px}

/* footer */
.site-footer{left:0;top:2960px;width:1200px;height:430px;background:var(--night)}
.footer-head{position:absolute;top:3012px;font-family:"Orbitron",sans-serif;font-size:21px;letter-spacing:3px;color:#fff;text-transform:uppercase}
.links{position:absolute;left:84px;top:3066px;list-style:none}
.links li{font-size:13px;color:#ddd;height:36px}
.divider{position:absolute;top:3005px;width:1px;height:270px;background:#444}
.contact-row{position:absolute;left:402px;display:flex;gap:18px;align-items:flex-start}
.contact-row p{font-size:13px;line-height:18px;color:#ddd}
.field{position:absolute;border:1px solid #666;font-size:12px;color:#ccc;padding:10px 14px}
.submit{position:absolute;left:990px;top:3227px;width:120px;height:43px;background:var(--coral);color:#fff;font-size:13px;display:flex;align-items:center;justify-content:center;gap:6px}
.footer-rule{left:0;top:3322px;width:1200px;height:1px;background:#333}
.copyright{left:0;top:3350px;width:1200px;text-align:center;font-size:12px;color:#bbb}
.copyright span{color:var(--coral);font-family:"Orbitron",sans-serif;letter-spacing:2px}
</style>
</head>
<body>

<header class="site-header">
  <div class="abs brand">KELTO CONSTRUCTION</div>
  <nav class="nav">
    <a class="current" style="left:0">HOME</a>
    <a style="left:108px">ABOUT US</a>
    <a style="left:236px">PROJECTS</a>
    <a style="left:358px">BLOGS</a>
    <a style="left:466px">CONTACT US</a>
  </nav>
</header>

<section class="abs hero" role="img" aria-label="Photograph of a curving white modern building under a dusk sky"></section>
<div class="abs hero-panel"></div>
<div class="abs heading hero-brand">KELTO</div>
<h1 class="abs hero-title">WE HAVE NEW FRESH IDEAS ALL THE TIME</h1>
<p class="abs hero-copy">Lorem Ipsum is simply dummy text of the printing and typesetting industry. Lorem Ipsum has been the industry's standard dummy text ever since the 1500</p>
<div class="btn hero-btn">Get Started Now</div>
<div class="slider-arrow" style="left:12px;top:388px">
  <svg width="18" height="18" viewBox="0 0 18 18"><path d="M11 3 5 9l6 6" stroke="#fff" stroke-width="2" fill="none"/></svg>
</div>
<div class="slider-arrow" style="left:1134px;top:388px">
  <svg width="18" height="18" viewBox="0 0 18 18"><path d="m7 3 6 6-6 6" stroke="#fff" stroke-width="2" fill="none"/></svg>
</div>

<section>
  <h2 class="abs heading about-title">About Us</h2>
  <p class="abs body-copy about-copy">Lorem Ipsum is simply dummy text of the printing and typesetting industry. Lorem Ipsum has been the industry's standard dummy text ever since the 1500s, when an unknown printer took a galley of type and scrambled it to make a type specimen book. It has survived not only five centuries, but also the leap into electronic typesetting, remaining essentially unchanged. It was popularised in the 1960.</p>
  <div class="btn about-btn">Read More</div>
  <div class="frame" style="left:631px;top:690px;width:524px;height:424px"></div>
  <div class="photo" style="left:597px;top:660px;width:528px;height:426px;background:#fff;box-shadow:0 2px 8px rgba(0,0,0,.15)"></div>
  <div class="photo" role="img" aria-label="Photograph of two builders in hard hats reviewing plans on site" style="left:607px;top:670px;width:508px;height:406px;background:linear-gradient(135deg,#d8dde2,#c9a47a 55%,#e8743a)"></div>
</section>

<section class="abs projects"></section>
<div class="frame" style="left:77px;top:1281px;width:190px;height:419px;border-right:none"></div>
<div class="photo" style="left:127px;top:1217px;width:530px;height:423px;background:#fff;box-shadow:0 2px 8px rgba(0,0,0,.12)"></div>
<div class="photo" role="img" aria-label="Photograph of a dark clad modern two-storey house at dusk" style="left:135px;top:1225px;width:514px;height:407px;background:linear-gradient(180deg,#7d97b2 0%,#a9b7c4 40%,#2c2f33 70%,#6b6a5c 100%)"></div>
<h2 class="abs heading projects-title">Projects</h2>
<p class="abs body-copy projects-copy">Lorem Ipsum is simply dummy text of the printing and typesetting industry. Lorem Ipsum has been the industry's standard dummy text ever since the 1500s, when an unknown printer took a galley of type and scrambled it to make a type specimen book.</p>
<div class="btn projects-btn">View All Projects</div>
<svg class="abs" style="left:566px;top:1672px" width="72" height="16" viewBox="0 0 72 16">
  <path d="M16 8H2m5-5L2 8l5 5" stroke="#e8584a" stroke-width="2" fill="none"/>
  <path d="M48 8h14m-5-5 5 5-5 5" stroke="#222" stroke-width="2" fill="none"/>
</svg>
<div class="thumb" role="img" aria-label="Photograph of a green-roofed curved building by a harbour" style="left:77px;background:linear-gradient(135deg,#6f8fa8,#5d7f3c 60%,#8a8f6a)"></div>
<div class="thumb" role="img" aria-label="Photograph of an angular glass facade against blue sky" style="left:346px;background:linear-gradient(135deg,#2d5fa8,#9ec3e6 55%,#c8c0b8)"></div>
<div class="thumb" role="img" aria-label="Photograph of a white office tower with an orange accent" style="left:612px;background:linear-gradient(135deg,#e8ecef,#c7cbcf 60%,#c04a2a)"></div>
<div class="thumb" role="img" aria-label="Photograph of a bright minimalist interior" style="left:879px;background:linear-gradient(135deg,#d9d9d9,#9a9a9a 60%,#e6e6e6)"></div>

<section class="abs testimonial"></section>
<div class="abs quote-box"></div>
<p class="abs quote">"Lorem Ipsum is simply dummy text of the printing and typesetting industry. Lorem Ipsum has been the industry's standard dummy text ever since the 1500s,Lorem Ipsum is simply dummy text of the printing and typesetting industry."</p>
<div class="abs cite">~ CUSTOMER NAME</div>
<div class="abs cite-role">Company</div>
<div class="abs avatar" role="img" aria-label="Customer portrait"></div>
<span class="dot" style="left:580px"></span>
<span class="dot" style="left:595px;background:#fff"></span>
<span class="dot" style="left:610px"></span>

<section>
  <h2 class="abs heading blogs-title">Blogs</h2>

  <div class="post-img" role="img" aria-label="Photograph of a row of sharp timber gables" style="top:2531px;background:linear-gradient(180deg,#d3d8dc,#5a4a3a 70%,#7a7a70)"></div>
  <div class="post-date" style="top:2548px">
    <svg width="16" height="16" viewBox="0 0 16 16"><rect x="1" y="3" width="14" height="12" fill="none" stroke="#999"/><path d="M1 7h14M5 1v4m6-4v4" stroke="#999"/></svg>26,FEB, 2018
  </div>
  <div class="post-title" style="top:2582px">Lorem Ipsum is simply dummy.</div>
  <p class="post-copy" style="top:2612px">Lorem Ipsum is simply dummy text of the printing and typesetting...</p>
  <div class="post-more" style="top:2671px">READ MORE »</div>

  <div class="post-img" role="img" aria-label="Photograph of a patterned residential tower against the sky" style="top:2719px;background:linear-gradient(180deg,#c9d3dc,#3a3a3a 55%,#8c8c8c)"></div>
  <div class="post-date" style="top:2736px">
    <svg width="16" height="16" viewBox="0 0 16 16"><rect x="1" y="3" width="14" height="12" fill="none" stroke="#999"/><path d="M1 7h14M5 1v4m6-4v4" stroke="#999"/></svg>15,MARCH, 2018
  </div>
  <div class="post-title" style="top:2770px">Lorem Ipsum is simply dummy.</div>
  <p class="post-copy" style="top:2800px">Lorem Ipsum is simply dummy text of the printing and typesetting...</p>
  <div class="post-more" style="top:2859px">READ MORE »</div>

  <div class="frame" style="left:1060px;top:2479px;width:63px;height:414px;border-left:none"></div>
  <div class="photo" role="img" aria-label="Photograph of a geometric glass building facade" style="left:554px;top:2420px;width:513px;height:407px;background:linear-gradient(135deg,#5d7f86,#c5cdd0 50%,#6e8a90)"></div>
  <div class="abs feature-card"></div>
  <div class="abs date-badge"><div style="font-size:32px;margin-top:10px">17</div><div style="font-size:13px;margin-top:2px">MARCH</div></div>
  <div class="abs feature-title">Lorem Ipsum is simply dummy.</div>
  <p class="abs feature-copy">Lorem Ipsum is simply dummy text of the printing and typesetting industry. Lorem Ipsum has been the industry's standard dummy text ever since the 1500s, when an unknown printer took a galley of type and scrambled it.</p>
  <div class="btn feature-btn">Read More</div>
</section>

<footer class="abs site-footer">
</footer>
<div class="footer-head" style="left:81px">Usefull Links</div>
<ul class="links">
  <li>› Home</li><li>› About Us</li><li>› Projects</li><li>› Blogs</li><li>› Contact Us</li><li>› Login</li>
</ul>
<div class="divider" style="left:334px"></div>
<div class="divider" style="left:658px"></div>
<div class="footer-head" style="left:402px">Contat Us</div>
<div class="contact-row" style="top:3064px">
  <svg width="22" height="34" viewBox="0 0 22 34"><rect x="2" y="1" width="18" height="32" rx="3" fill="none" stroke="#e8584a" stroke-width="2"/><path d="M8 28h6" stroke="#e8584a" stroke-width="2"/></svg>
  <p>CALL NOW<br>123 456 7878</p>
</div>
<div class="contact-row" style="top:3138px">
  <svg width="36" height="26" viewBox="0 0 36 26"><rect x="1" y="1" width="34" height="24" fill="none" stroke="#e8584a" stroke-width="2"/><path d="m1 1 17 14L35 1M1 25l12-12m22 12L23 13" stroke="#e8584a" stroke-width="2" fill="none"/></svg>
  <p>GENERAL QUESTIONS<br>info@keltoconstruction.example.com</p>
</div>
<div class="contact-row" style="top:3208px">
  <svg width="30" height="34" viewBox="0 0 30 34"><path d="M15 31S5 20 5 12a10 10 0 0 1 20 0c0 8-10 19-10 19z" fill="none" stroke="#e8584a" stroke-width="2"/><circle cx="15" cy="12" r="4" fill="none" stroke="#e8584a" stroke-width="2"/></svg>
  <p>123,Lorem ipsum dummy text.<br>Country - 123456.</p>
</div>
<div class="footer-head" style="left:719px">Send Us Message</div>
<div class="field" style="left:721px;top:3067px;width:183px;height:52px">Name*</div>
<div class="field" style="left:927px;top:3067px;width:183px;height:52px">Email Address*</div>
<div class="field" style="left:721px;top:3139px;width:389px;height:70px">Message*</div>
<div class="field" style="left:721px;top:3227px;width:183px;height:50px">Name*</div>
<div class="submit">SUBMIT
  <svg width="14" height="10" viewBox="0 0 14 10"><path d="M0 5h12M8 1l4 4-4 4" stroke="#fff" stroke-width="1.6" fill="none"/></svg>
</div>
<div class="abs footer-rule"></div>
<div class="abs copyright">© <span>KELTO CONSTRUCTIONS.</span> - 2018 All Right Reserved</div>

</body>
</html>
```